Business card design for Automotive workshop

We need a business card for a new automotive repair and tyre shop called Keelstone Prime Automotive located in New Zealand. We are a clean, modern and fresh workshop and company.

Front needs to feature logo,
my name:
Marlo Fenwicke (director)

Address:
48 Tarn Lane
Harrowvale 3642

Phone: 07 594 2713
Mobile: 027 451 9362
Email: office@keelstoneautomotive.example.nz
Website: keelstoneautomotive.example.nz

Back needs to feature an area to write down appointment details, date and time.

Also feature a list of jobs and work we do such as,
Vehicle Servicing
All Mechanical Repairs
Warrant of Fitness
Tyres & Wheel Alignments
Automotive Diagnostics
Automotive Parts & Supplies

```html
<!DOCTYPE html>
<html lang="en">
<head>
<meta charset="utf-8">
<title>Keelstone Prime Automotive – Business Card</title>
<link href="https://fonts.googleapis.com/css2?family=Roboto:wght@400;500;700&display=swap" rel="stylesheet">
<style>
  :root {
    --red: #e31e26;
    --ink: #1a1a1a;
    --card-dark: #151515;
    --white: #ffffff;
    --stage: #4a4a4a;
    --rule: #8a8a8a;
  }
  * { margin: 0; padding: 0; box-sizing: border-box; }
  html, body { width: 1200px; height: 1200px; overflow: hidden; }
  body {
    background: var(--stage);
    font-family: 'Roboto', Arial, sans-serif;
    position: relative;
  }
  .card {
    position: absolute;
    left: 263px;
    width: 664px;
    height: 389px;
    overflow: hidden;
  }
  .card-front { top: 199px; background: var(--card-dark); }
  .card-back { top: 624px; background: var(--white); }

  .wordmark {
    position: absolute;
    left: 0; right: 0;
    text-align: center;
    font-weight: 700;
    font-size: 31px;
    letter-spacing: 2px;
    text-transform: uppercase;
    line-height: 1;
    color: var(--red);
  }
  .card-front .wordmark { top: 85px; }
  .card-back .wordmark { top: 48px; }

  .person {
    position: absolute;
    right: 370px;
    top: 222px;
    text-align: right;
  }
  .person-name { color: var(--red); font-weight: 700; font-size: 26px; line-height: 1.1; }
  .person-role { color: var(--white); font-size: 17px; line-height: 1.1; }

  .divider {
    position: absolute;
    left: 320px; top: 206px;
    width: 1px; height: 86px;
    background: var(--white);
  }
  .contacts {
    position: absolute;
    left: 340px; top: 200px;
    list-style: none;
    color: var(--white);
    font-size: 15.5px;
  }
  .contacts li { display: flex; align-items: center; height: 24.5px; white-space: nowrap; }
  .contacts svg { width: 11px; height: 11px; margin-right: 6px; flex: none; }

  .address-band {
    position: absolute;
    left: 0; right: 0; bottom: 0;
    height: 57px;
    background: var(--red);
    color: var(--white);
    font-size: 17.5px;
    display: flex; align-items: center; justify-content: center;
  }

  .appointment-title {
    position: absolute;
    left: 0; right: 0; top: 145px;
    text-align: center;
    color: var(--red);
    font-size: 24px;
    font-weight: 500;
  }
  .field {
    position: absolute;
    display: flex;
    align-items: flex-end;
    color: var(--ink);
    font-size: 21px;
  }
  .field .line {
    flex: 1;
    border-bottom: 1px solid var(--rule);
    margin-left: 3px;
    margin-bottom: 4px;
  }
  .field-date { left: 38px; width: 291px; }
  .field-time { left: 336px; width: 293px; }
  .row-1 { top: 200px; }
  .row-2 { top: 247px; }

  .days {
    position: absolute;
    left: 102px; top: 290px;
    display: flex;
    list-style: none;
    font-size: 20px;
    color: var(--ink);
  }
  .days li { display: flex; align-items: center; margin-right: 26px; }
  .days li:last-child { margin-right: 0; }
  .days .circle {
    width: 19px; height: 19px;
    border: 1.3px solid var(--red);
    border-radius: 50%;
    margin-right: 3px;
  }
  .services-band {
    position: absolute;
    left: 0; right: 0; bottom: 0;
    height: 60px;
    background: var(--card-dark);
    border-top: 2px solid var(--red);
    color: var(--white);
    font-size: 16px;
    text-align: center;
    padding-top: 6px;
    line-height: 19px;
  }
  .services-band .dot { color: var(--red); margin: 0 4px 0 6px; }
</style>
</head>
<body>
  <section class="card card-front">
    <div class="wordmark">Keelstone Prime Automotive</div>

    <div class="person">
      <div class="person-name">Marlo Fenwicke</div>
      <div class="person-role">Owner</div>
    </div>
    <div class="divider"></div>

    <ul class="contacts">
      <li>
        <svg viewBox="0 0 12 12"><path fill="#e31e26" d="M2.5 0.5l2 2.2-1 1.3c.6 1.5 1.8 2.8 3.3 3.5l1.3-1 2.2 2-1.2 2.2C5 10.5 1.5 7 0.3 1.7z"/></svg>
        07 594 2713
      </li>
      <li>
        <svg viewBox="0 0 12 12"><rect x="3" y="0.5" width="6" height="11" rx="1" fill="none" stroke="#e31e26" stroke-width="1.3"/><rect x="5" y="9" width="2" height="1" fill="#e31e26"/></svg>
        027 451 9362
      </li>
      <li>
        <svg viewBox="0 0 12 12"><rect x="0.5" y="2.5" width="11" height="7" fill="#e31e26"/><path d="M0.5 2.5l5.5 4 5.5-4" fill="none" stroke="#151515" stroke-width="1"/></svg>
        office@keelstoneautomotive.example.nz
      </li>
      <li>
        <svg viewBox="0 0 12 12"><g fill="none" stroke="#e31e26" stroke-width="1"><circle cx="6" cy="6" r="5"/><ellipse cx="6" cy="6" rx="2.2" ry="5"/><path d="M1 6h10M2 3.3h8M2 8.7h8"/></g></svg>
        keelstoneautomotive.example.nz
      </li>
    </ul>

    <div class="address-band">48 Tarn Lane, Harrowvale 3642</div>
  </section>

  <section class="card card-back">
    <div class="wordmark">Keelstone Prime Automotive</div>

    <h2 class="appointment-title">APPOINTMENT</h2>

    <div class="field field-date row-1">Date:<span class="line"></span></div>
    <div class="field field-time row-1">Time:<span class="line"></span></div>
    <div class="field field-date row-2">Date:<span class="line"></span></div>
    <div class="field field-time row-2">Time:<span class="line"></span></div>

    <ul class="days">
      <li><span class="circle"></span>Mon</li>
      <li><span class="circle"></span>Tue</li>
      <li><span class="circle"></span>Wed</li>
      <li><span class="circle"></span>Thur</li>
      <li><span class="circle"></span>Fri</li>
      <li><span class="circle"></span>Sat</li>
    </ul>

    <div class="services-band">
      <div><span class="dot">•</span>Vehicle Servicing <span class="dot">•</span>All Mechanical Repairs <span class="dot">•</span>Warrant of Fitness</div>
      <div><span class="dot">•</span>Tyres &amp; Wheel Alignments <span class="dot">•</span>Automotive Diagnostics <span class="dot">•</span>Automotive Parts &amp; Supplies</div>
    </div>
  </section>
</body>
</html>
```